Fitness website

Website for a fitness brand (see attached specs). Design needs to be modern and vibrant with CTAs on every page. We will provide logos, images, etc but for now user placeholder text and images. For now use the name 'Corvane Athletics' as the name to use on the design. The goal of this site is to either get people to join the gym (5 physical locations across the US); buy an online program; buy merch or supplements or sign up for the newsletter. Pleas use images from this foldeR: https://filebarn.example/share/folders/8QwTz41mKpLrXv93NdYe7HsaBuJ0Cf2_R?usp=sharing

We will be coding this in ReactNative. Lots more work for the winner as well, this is a 1st project for us.

Target Market(s)

fitness enthusiats

Industry/Entity Type

fitness, health, wellness

Number of Pages Required

5+ page

Font styles to use
Other font styles liked:
• Lato

Colors
0054AA
0677BA
7BADD7
CADEEF
E8F1F8
0094D4
00A9DD
6FCCEA
C7EBF8
E9F6FB
00AB8E
00BBA5
67D7C9
C6EFE9
E9F9F6
EE7325
F08F49
F5BC92
FAE3D3
FDF4ED

Requirements
Must have
• must be reactive. most people will view it first on mobile
Nice to have
• video in hero section of top of home page

```html
<!DOCTYPE html>
<html lang="en">
<head>
<meta charset="utf-8">
<title>Corvane Athletics</title>
<link href="https://fonts.googleapis.com/css2?family=Barlow:wght@500;600;700;800&family=Barlow+Semi+Condensed:wght@500;600;700&family=Lato:wght@400;700&display=swap" rel="stylesheet">
<style>
:root{
  --blue:#0054AA;
  --blue-2:#0677BA;
  --blue-light:#7BADD7;
  --teal:#00AB8E;
  --teal-2:#00BBA5;
  --orange:#EE7325;
  --orange-2:#F08F49;
  --ink:#1b1b1b;
  --text:#444;
  --muted:#777;
  --white:#fff;
  --line:#dfe6ee;
}
*{margin:0;padding:0;box-sizing:border-box}
html,body{width:1200px;height:4501px;overflow:hidden}
body{position:relative;font-family:"Lato",sans-serif;color:var(--text);background:var(--white)}
.abs{position:absolute}
.head{font-family:"Barlow",sans-serif;font-weight:700;color:var(--ink);text-transform:uppercase}
.center{text-align:center}

/* header */
.site-header{left:0;top:0;width:1200px;height:68px;background:var(--white);box-shadow:0 2px 8px rgba(0,0,0,.06);z-index:5}
.brand{left:63px;top:20px;font-family:"Barlow",sans-serif;font-weight:700;font-size:21px;color:var(--blue);letter-spacing:.3px}
.main-nav{left:305px;top:24px;display:flex}
.main-nav a{font-family:"Barlow Semi Condensed",sans-serif;font-weight:700;font-size:13px;color:#222;text-decoration:none;text-transform:uppercase;margin-right:35px;position:relative}
.main-nav a.active{color:var(--orange)}
.main-nav a.active::after{content:"";position:absolute;left:0;right:0;bottom:-6px;height:2px;background:var(--orange)}
.contact-btn{left:1045px;top:0;width:155px;height:68px;background:var(--orange);color:#fff;font-family:"Barlow Semi Condensed",sans-serif;font-weight:700;font-size:13px;display:flex;align-items:center;justify-content:center}

/* hero */
.hero-media{left:0;top:68px;width:1200px;height:689px;background:linear-gradient(90deg,#0a4a9c 0%,#0c5bb5 38%,#2d5d92 55%,#4b5866 75%,#6b6f76 100%)}
.hero-label{left:96px;top:258px;color:#fff;font-family:"Barlow",sans-serif;font-weight:500;font-size:25px;letter-spacing:2px}
.hero-title{left:96px;top:296px;color:#fff;font-family:"Barlow",sans-serif;font-weight:800;font-size:58px;line-height:60px}
.btn{display:flex;align-items:center;justify-content:center;font-family:"Barlow Semi Condensed",sans-serif;font-weight:700;font-size:13px;text-transform:uppercase;color:#fff}
.btn-orange{background:var(--orange)}
.btn-outline{border:2px solid #fff}
.scroll-hex{left:571px;top:727px}

/* about */
.about-label{left:660px;top:888px;font-family:"Barlow Semi Condensed",sans-serif;font-weight:700;font-size:14px;color:var(--blue)}
.about-title{left:656px;top:914px;font-size:42px;line-height:44px;font-weight:800}
.about-copy{left:664px;top:1024px;width:510px;font-size:18.5px;line-height:27px;color:#333}
.side-rule{left:0;top:1300px;width:2px;height:120px;background:var(--blue)}

/* programs */
.programs-band{left:0;top:1420px;width:1200px;height:415px;background:linear-gradient(90deg,#0058b0 0%,#0677BA 45%,#00AB8E 100%)}
.watermark{left:0;top:1420px;width:1200px;text-align:center;font-family:"Barlow",sans-serif;font-weight:700;font-size:104px;letter-spacing:6px;color:transparent;-webkit-text-stroke:1.5px rgba(255,255,255,.28)}
.section-label{font-family:"Barlow Semi Condensed",sans-serif;font-weight:700;font-size:14px;text-transform:uppercase;left:0;width:1200px;text-align:center}
.section-title{left:0;width:1200px;text-align:center;font-family:"Barlow",sans-serif;font-weight:700;font-size:42px;text-transform:uppercase}
.program-photo{position:absolute;width:313px;height:240px}
.program-box{position:absolute;top:1795px;width:265px;height:168px;background:#fff;clip-path:polygon(0 38px,50% 0,100% 38px,100% 100%,0 100%);box-shadow:0 6px 14px rgba(0,0,0,.1)}
.program-icon{position:absolute;width:58px;height:58px;border-radius:50%;display:flex;align-items:center;justify-content:center;border:3px solid #fff}
.program-name{position:absolute;width:265px;text-align:center;font-family:"Barlow",sans-serif;font-weight:600;font-size:19px;color:#111}
.program-text{position:absolute;width:265px;text-align:center;font-size:12px;line-height:18px;color:#555}
.program-rule{position:absolute;width:265px;height:2px}
.dot-btn{position:absolute;width:24px;height:24px;border-radius:50%;display:flex;align-items:center;justify-content:center}
.slider-arrow{top:1722px}

/* shop */
.product-card{top:2210px;width:309px;height:341px;background:linear-gradient(135deg,#f6f7f9 0%,#e9ecef 30%,#fafafa 50%,#e7eaee 70%,#f5f6f8 100%);border:1px solid var(--line)}
.product-card.active{border:2px solid var(--blue)}
.product-media{position:absolute;left:80px;top:24px;width:150px;height:196px;border-radius:6px}
.product-name{position:absolute;left:0;top:243px;width:100%;text-align:center;font-family:"Barlow",sans-serif;font-weight:600;font-size:19px;color:#111}
.product-text{position:absolute;left:0;top:271px;width:100%;text-align:center;font-family:"Barlow Semi Condensed",sans-serif;font-size:12.5px;color:#444}
.product-price{position:absolute;left:0;top:293px;width:100%;text-align:center;font-family:"Barlow",sans-serif;font-weight:700;font-size:23px;color:var(--blue)}
.round-arrow{top:2583px;width:44px;height:44px;border-radius:50%;display:flex;align-items:center;justify-content:center}

/* split cta */
.cta-left{left:0;top:2757px;width:606px;height:470px;background:linear-gradient(120deg,#f07a2c 0%,#ee7325 50%,#e9691d 100%)}
.cta-right{left:606px;top:2757px;width:594px;height:470px;background:linear-gradient(120deg,#1a66be 0%,#0054AA 55%,#0a4c9c 100%)}
.cta-title{font-family:"Barlow",sans-serif;font-weight:700;font-size:38px;line-height:42px;color:#fff;text-transform:uppercase;text-align:center}
.cta-text{font-size:14px;line-height:27px;color:#fff;text-align:center}

/* testimonials */
.quote-card{top:3410px;height:276px;background:#fff;box-shadow:0 4px 18px rgba(0,0,0,.1)}
.quote-card.featured{background:var(--blue)}
.quote-text{position:absolute;left:34px;top:72px;width:260px;font-size:14px;line-height:23px;color:#555}
.featured .quote-text,.featured .quote-name,.featured .quote-loc{color:#fff}
.quote-avatar{position:absolute;left:38px;top:200px;width:40px;height:40px;border-radius:50%}
.quote-name{position:absolute;left:90px;top:198px;font-size:12.5px;font-weight:700;color:#222}
.quote-loc{position:absolute;left:90px;top:216px;font-size:11.5px;color:#777}
.quote-stars{position:absolute;left:90px;top:234px;font-size:11px;letter-spacing:3px;color:#f5b400}

/* newsletter */
.footer-bg{left:0;top:4011px;width:1200px;height:490px;background:var(--blue)}
.newsletter{left:105px;top:3784px;width:990px;height:306px;background:linear-gradient(110deg,#ee7325 0%,#f08f49 45%,#ee7325 100%)}
.newsletter-label{left:105px;top:3852px;width:990px;text-align:center;font-family:"Barlow",sans-serif;font-weight:500;font-size:16px;color:#fff;opacity:.9}
.newsletter-title{left:105px;top:3876px;width:990px;text-align:center;font-family:"Barlow",sans-serif;font-weight:700;font-size:42px;color:#fff}
.email-field{left:267px;top:3954px;width:510px;height:57px;background:#fff;padding-left:26px;display:flex;align-items:center;font-size:15px;color:#333}
.subscribe{left:784px;top:3954px;width:179px;height:57px;background:var(--blue);font-size:15px}

/* footer */
.footer-brand{left:118px;top:4172px;width:226px;text-align:center;font-family:"Barlow",sans-serif;font-weight:700;font-size:34px;line-height:41px;color:#fff}
.social{top:4274px;width:26px;height:26px;border-radius:50%;background:#fff}
.footer-head{top:4164px;font-family:"Barlow",sans-serif;font-weight:700;font-size:20px;color:#fff;text-transform:uppercase}
.footer-list{list-style:none}
.footer-list li{font-size:14px;color:#fff;height:27px;line-height:27px}
.footer-list li::before{content:"» "}
.contact-line{left:879px;font-size:14px;color:#fff;display:flex;align-items:center;gap:12px}
.footer-rule{left:128px;top:4414px;width:944px;border-top:1px dashed rgba(255,255,255,.5)}
.to-top{left:1073px;top:4399px;width:32px;height:32px;border-radius:50%;background:var(--orange);display:flex;align-items:center;justify-content:center}
.copyright{left:0;top:4444px;width:1200px;text-align:center;font-size:11px;color:#fff}
</style>
</head>
<body>

<header class="abs site-header">
  <div class="abs brand">CORVANE ATHLETICS</div>
  <nav class="abs main-nav">
    <a class="active">Home</a><a>About Us</a><a>Programs</a><a>Shop</a><a>Locations</a><a>Affiliate</a><a>Blog</a><a>Members</a>
  </nav>
  <div class="abs contact-btn">CONTACT US &nbsp;›</div>
</header>

<div class="abs hero-media" role="img" aria-label="Athlete lifting a loaded barbell in a gym, blue overlay on the left"></div>
<div class="abs hero-label">CORVANE ATHLETICS</div>
<h1 class="abs hero-title">UNLEASH YOUR<br>INNER CHAMPION</h1>
<div class="abs btn btn-orange" style="left:96px;top:445px;width:184px;height:48px">JOIN THE GYM &nbsp;›</div>
<div class="abs btn btn-outline" style="left:290px;top:445px;width:184px;height:48px">BUY PROGRAM &nbsp;›</div>
<svg class="abs scroll-hex" width="60" height="64" viewBox="0 0 60 64">
  <polygon points="30,2 57,17 57,47 30,62 3,47 3,17" fill="#fff"/>
  <path d="M30 20 V42 M21 34 L30 43 L39 34" stroke="#0054AA" stroke-width="2.2" fill="none"/>
</svg>

<svg class="abs" style="left:0;top:800px" width="640" height="560" viewBox="0 800 640 560">
  <defs>
    <linearGradient id="aboutA" x1="0" y1="0" x2="1" y2="1"><stop offset="0" stop-color="#3a4a58"/><stop offset=".55" stop-color="#5b5a4e"/><stop offset="1" stop-color="#1e2a3a"/></linearGradient>
    <linearGradient id="aboutB" x1="0" y1="0" x2="1" y2="1"><stop offset="0" stop-color="#8a8f95"/><stop offset="1" stop-color="#4c5560"/></linearGradient>
  </defs>
  <polygon points="52,1048 180,823 455,823 576,1048 455,1275 180,1275" fill="none" stroke="#7BADD7" stroke-width="2.5"/>
  <polygon points="75,1048 195,843 440,843 556,1048 440,1255 195,1255" fill="url(#aboutA)" role="img" aria-label="Athlete training in the gym"/>
  <polygon points="340,1214 404,1097 550,1097 611,1214 550,1331 404,1331" fill="url(#aboutB)" stroke="#fff" stroke-width="6" role="img" aria-label="Athlete skipping rope in the gym"/>
</svg>
<div class="abs side-rule"></div>
<div class="abs about-label">BUILT FOR ATHLETES. DESIGNED FOR EVERYONE.</div>
<h2 class="abs head about-title">ABOUT CORVANE<br>ATHLETICS</h2>
<p class="abs about-copy">Corvane Athletics is more than a gym — it’s a movement. With 5 state-of-the-art training centers across the U.S. and a powerful online coaching platform, we help athletes and everyday warriors reach their next level. Whether you want to build strength, improve endurance, or transform your lifestyle — we’ve got your back.</p>
<div class="abs btn btn-orange" style="left:662px;top:1216px;width:175px;height:42px">LEARN MORE &nbsp;›</div>

<div class="abs programs-band"></div>
<div class="abs watermark">PROGRAMS</div>
<div class="abs section-label" style="top:1491px;color:#fff">CHOOSE YOUR PATH TO GREATNESS</div>
<h2 class="abs section-title" style="top:1508px;color:#fff">OUR TRAINING PROGRAMS</h2>

<svg class="abs slider-arrow" style="left:48px" width="30" height="56" viewBox="0 0 30 56"><path d="M26 2 L4 28 L26 54" stroke="#fff" stroke-width="3" fill="none"/></svg>
<svg class="abs slider-arrow" style="left:1134px" width="30" height="56" viewBox="0 0 30 56"><path d="M4 2 L26 28 L4 54" stroke="#fff" stroke-width="3" fill="none"/></svg>

<div class="abs program-photo" style="left:115px;top:1612px;background:linear-gradient(135deg,#4d5a68,#2b3440 60%,#6e7682)" role="img" aria-label="Athlete deadlifting a barbell"></div>
<div class="abs program-photo" style="left:454px;top:1612px;background:linear-gradient(135deg,#5a4e44,#2e2a28 60%,#6c6258)" role="img" aria-label="Athletes training functional movements"></div>
<div class="abs program-photo" style="left:795px;top:1612px;background:linear-gradient(135deg,#6f7a5a,#3f4a36 55%,#a69a7e)" role="img" aria-label="Healthy meal bowl with vegetables"></div>

<div class="abs program-box" style="left:140px"></div>
<div class="abs program-box" style="left:479px"></div>
<div class="abs program-box" style="left:820px"></div>

<div class="abs program-icon" style="left:243px;top:1772px;background:var(--blue-2)">
  <svg width="26" height="26" viewBox="0 0 26 26"><path d="M5 18 C5 10 11 6 15 8 L17 12 L13 13 C16 14 20 15 21 18 Z" fill="#fff"/></svg>
</div>
<div class="abs program-icon" style="left:582px;top:1772px;background:var(--orange)">
  <svg width="28" height="20" viewBox="0 0 28 20"><rect x="2" y="5" width="4" height="10" fill="#fff"/><rect x="7" y="2" width="3" height="16" fill="#fff"/><rect x="10" y="9" width="8" height="2" fill="#fff"/><rect x="18" y="2" width="3" height="16" fill="#fff"/><rect x="22" y="5" width="4" height="10" fill="#fff"/></svg>
</div>
<div class="abs program-icon" style="left:923px;top:1772px;background:var(--blue-2)">
  <svg width="24" height="26" viewBox="0 0 24 26"><rect x="3" y="4" width="14" height="19" rx="2" fill="none" stroke="#fff" stroke-width="2"/><rect x="7" y="2" width="6" height="4" fill="#fff"/><circle cx="17" cy="18" r="5" fill="#fff"/></svg>
</div>

<div class="abs program-name" style="left:140px;top:1855px">MASTERS</div>
<div class="abs program-name" style="left:479px;top:1855px">FUNCTIONAL FITNESS</div>
<div class="abs program-name" style="left:820px;top:1855px">NUTRITIONS</div>
<p class="abs program-text" style="left:140px;top:1887px">Lorem ipsum dolor sit amet, con-<br>sectetur adipiscing elit sed</p>
<p class="abs program-text" style="left:479px;top:1887px">Lorem ipsum dolor sit amet, con-<br>sectetur adipiscing elit sed</p>
<p class="abs program-text" style="left:820px;top:1887px">Lorem ipsum dolor sit amet, con-<br>sectetur adipiscing elit sed</p>
<div class="abs program-rule" style="left:140px;top:1962px;background:var(--blue)"></div>
<div class="abs program-rule" style="left:479px;top:1962px;background:var(--orange)"></div>
<div class="abs program-rule" style="left:820px;top:1962px;background:var(--blue)"></div>
<div class="abs dot-btn" style="left:261px;top:1951px;background:var(--blue)"><svg width="8" height="10"><path d="M2 1 L6 5 L2 9" stroke="#fff" stroke-width="2" fill="none"/></svg></div>
<div class="abs dot-btn" style="left:600px;top:1951px;background:var(--orange)"><svg width="8" height="10"><path d="M2 1 L6 5 L2 9" stroke="#fff" stroke-width="2" fill="none"/></svg></div>
<div class="abs dot-btn" style="left:941px;top:1951px;background:var(--blue)"><svg width="8" height="10"><path d="M2 1 L6 5 L2 9" stroke="#fff" stroke-width="2" fill="none"/></svg></div>

<div class="abs section-label" style="top:2085px;color:var(--blue)">BUY MERCH OR SUPPLEMENTS</div>
<h2 class="abs section-title" style="top:2103px;color:#111">SHOP CORVANE</h2>

<div class="abs product-card" style="left:-211px">
  <div class="product-media" style="background:linear-gradient(180deg,#9aa2aa,#5d656e)" role="img" aria-label="Supplement tub"></div>
  <div class="product-name">PRODUCT HEADING</div>
  <div class="product-text">LOREM IPSUM IS SIMPLY DUMMY TEXT</div>
</div>
<div class="abs product-card" style="left:131px">
  <div class="product-media" style="background:linear-gradient(180deg,#ffffff,#e4e6e9)" role="img" aria-label="White supplement pouch"></div>
  <div class="product-name">PRODUCT HEADING</div>
  <div class="product-text">LOREM IPSUM IS SIMPLY DUMMY TEXT</div>
  <div class="product-price">$59.99</div>
</div>
<div class="abs product-card active" style="left:459px">
  <div class="product-media" style="background:linear-gradient(180deg,#2a2a2a,#111)" role="img" aria-label="Black t-shirt and white mug"></div>
  <div class="product-name">PRODUCT HEADING</div>
  <div class="product-text">LOREM IPSUM IS SIMPLY DUMMY TEXT</div>
  <div class="product-price">$59.99</div>
</div>
<div class="abs product-card" style="left:795px">
  <div class="product-media" style="background:linear-gradient(180deg,#8e949b,#4f565e)" role="img" aria-label="Grey supplement tub"></div>
  <div class="product-name">PRODUCT HEADING</div>
  <div class="product-text">LOREM IPSUM IS SIMPLY DUMMY TEXT</div>
  <div class="product-price">$59.99</div>
</div>
<div class="abs product-card" style="left:1134px;top:2214px"></div>

<div class="abs round-arrow" style="left:555px;background:var(--blue)"><svg width="20" height="16"><path d="M19 8 H3 M9 2 L3 8 L9 14" stroke="#fff" stroke-width="2" fill="none"/></svg></div>
<div class="abs round-arrow" style="left:609px;background:var(--orange)"><svg width="20" height="16"><path d="M1 8 H17 M11 2 L17 8 L11 14" stroke="#fff" stroke-width="2" fill="none"/></svg></div>

<div class="abs cta-left" role="img" aria-label="Orange-toned gym background"></div>
<div class="abs cta-right" role="img" aria-label="Blue-toned gym background"></div>

<svg class="abs" style="left:264px;top:2800px" width="108" height="108" viewBox="0 0 108 108">
  <polygon points="54,4 98,29 98,79 54,104 10,79 10,29" fill="none" stroke="#fff" stroke-width="3"/>
  <rect x="37" y="34" width="26" height="36" rx="3" fill="none" stroke="#fff" stroke-width="3"/>
  <rect x="44" y="30" width="12" height="7" fill="#fff"/>
  <circle cx="66" cy="64" r="9" fill="#fff"/>
</svg>
<h2 class="abs cta-title" style="left:100px;top:2930px;width:430px">BUY AN ONLINE<br>PROGRAM</h2>
<p class="abs cta-text" style="left:80px;top:3016px;width:480px">Lorem ipsum dolor sit amet consectetur adipiscing elit, sed do eiusmod tempor incididunt ut labore et dolore</p>
<div class="abs btn btn-outline" style="left:250px;top:3085px;width:157px;height:46px">BUY NOW &nbsp;›</div>

<svg class="abs" style="left:839px;top:2800px" width="108" height="108" viewBox="0 0 108 108">
  <polygon points="54,4 98,29 98,79 54,104 10,79 10,29" fill="none" stroke="#fff" stroke-width="3"/>
  <g transform="rotate(-45 54 54)"><rect x="30" y="44" width="6" height="20" fill="#fff"/><rect x="38" y="40" width="5" height="28" fill="#fff"/><rect x="43" y="52" width="22" height="4" fill="#fff"/><rect x="65" y="40" width="5" height="28" fill="#fff"/><rect x="72" y="44" width="6" height="20" fill="#fff"/></g>
</svg>
<h2 class="abs cta-title" style="left:680px;top:2930px;width:440px">JOIN THE GYM</h2>
<p class="abs cta-text" style="left:680px;top:2978px;width:440px">Lorem ipsum dolor sit amet consectetur adipiscing elit, sed do eiusmod tempor incididunt ut labore et dolore</p>
<div class="abs btn btn-outline" style="left:826px;top:3052px;width:159px;height:44px">JOIN NOW &nbsp;›</div>

<div class="abs section-label" style="top:3306px;color:var(--blue)">TESTIMONIALS</div>
<h2 class="abs section-title" style="top:3323px;color:#111;left:-10px">SUCCESS STORIES</h2>

<div class="abs quote-card" style="left:91px;width:316px">
  <svg class="abs" style="left:40px;top:38px" width="36" height="26" viewBox="0 0 36 26"><path d="M2 24 V13 C2 6 6 2 13 1 V6 C9 7 8 9 8 12 H14 V24 Z M20 24 V13 C20 6 24 2 31 1 V6 C27 7 26 9 26 12 H32 V24 Z" fill="#0054AA"/></svg>
  <p class="quote-text">Lorem ipsum dolor sit amet, consec-tetur adipiscing elit, sed do eiusmod tempor incididunt ut labore et dolore magnaLorem ipsum dolor sit amet, consectetur adipiscing</p>
  <div class="quote-avatar" style="background:#8a7a6c" role="img" aria-label="Member photo"></div>
  <div class="quote-name">Dane Whitlow</div>
  <div class="quote-loc">City Location</div>
  <div class="quote-stars">★★★★★</div>
</div>
<div class="abs quote-card featured" style="left:430px;width:325px">
  <svg class="abs" style="left:40px;top:38px" width="36" height="26" viewBox="0 0 36 26"><path d="M2 24 V13 C2 6 6 2 13 1 V6 C9 7 8 9 8 12 H14 V24 Z M20 24 V13 C20 6 24 2 31 1 V6 C27 7 26 9 26 12 H32 V24 Z" fill="#fff"/></svg>
  <p class="quote-text">Lorem ipsum dolor sit amet, consec-tetur adipiscing elit, sed do eiusmod tempor incididunt ut labore et dolore magnaLorem ipsum dolor sit amet, consectetur adipiscing</p>
  <div class="quote-avatar" style="background:#b99a86" role="img" aria-label="Member photo"></div>
  <div class="quote-name">Mara K.</div>
  <div class="quote-loc">City Location</div>
  <div class="quote-stars">★★★★★</div>
</div>
<div class="abs quote-card" style="left:774px;width:318px">
  <svg class="abs" style="left:40px;top:38px" width="36" height="26" viewBox="0 0 36 26"><path d="M2 24 V13 C2 6 6 2 13 1 V6 C9 7 8 9 8 12 H14 V24 Z M20 24 V13 C20 6 24 2 31 1 V6 C27 7 26 9 26 12 H32 V24 Z" fill="#0054AA"/></svg>
  <p class="quote-text">Lorem ipsum dolor sit amet, consec-tetur adipiscing elit, sed do eiusmod tempor incididunt ut labore et dolore magnaLorem ipsum dolor sit amet, consectetur adipiscing</p>
  <div class="quote-avatar" style="background:#6f7f96" role="img" aria-label="Member photo"></div>
  <div class="quote-name">Mara K.</div>
  <div class="quote-loc">City Location</div>
  <div class="quote-stars">★★★★★</div>
</div>

<div class="abs footer-bg"></div>
<div class="abs newsletter" role="img" aria-label="Orange-toned gym background"></div>
<div class="abs newsletter-label">STAY FIT. STAY CONNECTED.</div>
<h2 class="abs newsletter-title">SIGN UP NEWSLETTER</h2>
<div class="abs email-field">Email address</div>
<div class="abs btn subscribe">SUBSCRIBE &nbsp;›</div>

<div class="abs footer-brand">CORVANE<br>ATHLETICS</div>
<div class="abs social" style="left:172px"></div>
<div class="abs social" style="left:210px"></div>
<div class="abs social" style="left:248px"></div>

<div class="abs footer-head" style="left:402px">Navigation</div>
<ul class="abs footer-list" style="left:402px;top:4199px"><li>Home</li><li>About Us</li><li>Programs</li><li>Shop</li><li>Locations</li></ul>
<ul class="abs footer-list" style="left:528px;top:4199px"><li>Affiliate</li><li>Blog</li><li>Members</li><li>Contact Us</li></ul>

<div class="abs footer-head" style="left:690px">Programs</div>
<ul class="abs footer-list" style="left:686px;top:4199px"><li>Masters</li><li>Functional Fitness</li><li>Competitive</li><li>Nutrition</li><li>Speciality</li><li>Race Prep</li></ul>

<div class="abs footer-head" style="left:879px">Contact Us</div>
<div class="abs contact-line" style="top:4209px">
  <svg width="22" height="22" viewBox="0 0 22 22"><path d="M5 2 L9 2 L10 7 L7 9 C8 12 10 14 13 15 L15 12 L20 13 L20 17 C20 19 18 20 16 20 C9 19 3 13 2 6 C2 4 3 2 5 2 Z" fill="#fff"/></svg>
  +1 (555) 214-3087
</div>
<div class="abs contact-line" style="top:4257px">
  <svg width="22" height="16" viewBox="0 0 22 16"><rect x="1" y="1" width="20" height="14" fill="#fff"/><path d="M1 1 L11 9 L21 1" stroke="#0054AA" stroke-width="1.5" fill="none"/></svg>
  info@corvaneathletics.com
</div>

<div class="abs footer-rule"></div>
<div class="abs to-top"><svg width="12" height="8"><path d="M1 7 L6 2 L11 7" stroke="#fff" stroke-width="2" fill="none"/></svg></div>
<div class="abs copyright">Copyright © 2025 Corvane Athletics. All Right Reserved</div>

</body>
</html>
```